Dynamic Business Card for Sports Supplements Company

Hi! I'm looking for an awesome business card to match my existing sports supplement company. I have uploaded my current company logo and screenshot of the front page of my website.

I would like to have something dynamic and interesting and utilize the colors in the website - the reds and purples

The business card should be double sided and focus on a unique eye-catching design on the back and include all the relevant company info.

Most importantly, it should say somewhere: "Sign up on our website for a coupon code."

Target Market(s)

Mostly for women gym goers but it shouldn't be too feminine. It should be in keeping with the website design. It should flow and clearly be connected to it

Industry/Entity Type

Business

Contact Information for Business Card

Lorraine K. Vestal
CEO
LVestal@Quorvanexco.com
www.quorvanexco.com
555.417.3820
P.O. Box 47315
Larkfield, Westmere 00000

Sign up on our website for a coupon code

Font styles to use
Serif
Sans Serif
Other font styles liked:
• Novecento font family and "Quorvanex" is in AR Destine font

Requirements
Must have
• One side should be a bold Quorvanex logo design. Even just the symbol itself may be o.k. (see attached file)

```html
<!DOCTYPE html>
<html lang="en">
<head>
<meta charset="utf-8">
<title>Quorvanex Business Card</title>
<link href="https://fonts.googleapis.com/css2?family=Open+Sans:wght@400;600;800&display=swap" rel="stylesheet">
<style>
  :root {
    --canvas: #ecebe8;
    --purple-dark: #2a2458;
    --purple: #4a3f8e;
    --purple-light: #5b4fa6;
    --red: #e3202e;
    --ink: #1b1b1b;
    --muted: #2f2f2f;
    --tagline-light: #dcd8f2;
    --white: #ffffff;
  }
  * { box-sizing: border-box; margin: 0; padding: 0; }
  html, body {
    width: 1200px; height: 900px; overflow: hidden;
    background: var(--canvas);
    font-family: "Open Sans", Arial, sans-serif;
  }
  .canvas {
    width: 1200px; height: 900px;
    display: flex; flex-direction: column; align-items: center; justify-content: center;
    gap: 40px;
  }
  .card {
    width: 680px; height: 389px; position: relative; overflow: hidden;
    box-shadow: 0 8px 24px rgba(0,0,0,0.18);
  }

  /* Back side */
  .card-back {
    background: radial-gradient(ellipse at 45% 35%, var(--purple-light) 0%, var(--purple) 45%, var(--purple-dark) 100%);
    color: var(--white); text-align: center;
  }
  .back-mark {
    width: 56px; height: 56px; border-radius: 50%;
    background: var(--red); margin: 62px auto 20px;
  }
  .back-name {
    font-weight: 800; font-size: 54px; letter-spacing: 2px; line-height: 1;
    text-transform: uppercase; color: var(--white);
  }
  .back-tagline {
    font-weight: 400; font-size: 15px; letter-spacing: 5px; text-transform: uppercase;
    margin-top: 8px; color: var(--tagline-light);
  }
  .back-signup {
    position: absolute; left: 0; right: 0; bottom: 70px;
    font-weight: 800; font-size: 18px; letter-spacing: 1.5px; text-transform: uppercase;
  }

  /* Front side */
  .card-front { background: var(--white); color: var(--ink); }
  .front-brand { position: absolute; left: 52px; top: 48px; }
  .front-name {
    font-weight: 800; font-size: 56px; letter-spacing: 1.5px; line-height: 1;
    text-transform: uppercase; color: var(--ink);
  }
  .front-tagline {
    font-size: 15px; letter-spacing: 5px; text-transform: uppercase; margin-top: 6px; color: var(--muted);
  }
  .person { position: absolute; left: 80px; top: 195px; }
  .person-name { color: var(--red); font-size: 24px; text-transform: uppercase; letter-spacing: 0.5px; }
  .person-role { font-size: 16px; margin-top: 2px; color: var(--muted); }
  .contact-list { list-style: none; margin-top: 22px; }
  .contact-list li {
    display: flex; align-items: center; gap: 10px;
    font-size: 17px; color: var(--muted); line-height: 1.55;
  }
  .contact-list svg { width: 14px; height: 14px; fill: var(--red); flex: none; }
  .address {
    position: absolute; right: 46px; top: 228px; text-align: right;
    font-size: 14px; line-height: 1.5; color: var(--muted); font-style: normal;
  }
</style>
</head>
<body>
<main class="canvas">
  <section class="card card-back" aria-label="Card back">
    <div class="back-mark"></div>
    <h1 class="back-name">Quorvanex</h1>
    <p class="back-tagline">Your Performance Partner</p>
    <p class="back-signup">Sign up on our website for a coupon code</p>
  </section>

  <section class="card card-front" aria-label="Card front">
    <div class="front-brand">
      <h2 class="front-name">Quorvanex</h2>
      <p class="front-tagline">Your Performance Partner</p>
    </div>
    <div class="person">
      <p class="person-name">Lorraine K. Vestal</p>
      <p class="person-role">CEO</p>
      <ul class="contact-list">
        <li>
          <svg viewBox="0 0 24 24" aria-hidden="true"><path d="M6.6 10.8a15.1 15.1 0 0 0 6.6 6.6l2.2-2.2a1 1 0 0 1 1-.25 11.4 11.4 0 0 0 3.6.57 1 1 0 0 1 1 1V20a1 1 0 0 1-1 1A17 17 0 0 1 3 4a1 1 0 0 1 1-1h3.5a1 1 0 0 1 1 1c0 1.25.2 2.45.57 3.6a1 1 0 0 1-.25 1z"/></svg>
          555.417.3820
        </li>
        <li>
          <svg viewBox="0 0 24 24" aria-hidden="true"><path d="M2 5h20v14H2z"/><path d="M2 5l10 8 10-8" fill="none" stroke="#fff" stroke-width="2"/></svg>
          LVestal@Quorvanexco.com
        </li>
        <li>
          <svg viewBox="0 0 24 24" aria-hidden="true"><circle cx="12" cy="12" r="10"/><path d="M2 12h20M12 2c3 3 3 17 0 20M12 2c-3 3-3 17 0 20" fill="none" stroke="#fff" stroke-width="1.5"/></svg>
          www.quorvanexco.com
        </li>
      </ul>
    </div>
    <address class="address">
      P.O. Box 47315<br>
      Larkfield, Westmere 00000
    </address>
  </section>
</main>
</body>
</html>
```